"Vine Hollow Excursions" is a top notch Santa Barbara County Wine Tour company.

We provide scenic, boutique and custom wine tours. I need the card to be clean and classy. I will provide our logo. I would like the logo to cover the back side of the card as an option and would like to see a couple color options other then our signature green and gold. I would like to see some creative options and let the designers come up with options.
I need cards for myself and my team. The final design should communicate "An authentic and boutique wine tour experience"
Please use my website for reference www.vinehollowexcursions.example

Target Market(s)

We have a wide range of clients from millennials to baby boomers

Industry/Entity Type

Tour

Contact Information for Business Card

Contact info:
Dale Morton
805-219-6384
info@vinehollowexcursions.example
vinehollowexcursions.example

Colors

Designer to choose colors to be used in the design.

Requirements
Must have
• my logo
Nice to have
• *I would like to have the backside side with the logo and the company statement
• "An authentic and boutique wine tour experience" as an option.
• *I would also like to see what the designers can create!
• *I would like to see an option that incorporates or social: instagram, yelp, trip advisor
Should not have
• I do not want it too busy.

```html
<!DOCTYPE html>
<html lang="en">
<head>
<meta charset="utf-8">
<title>Vine Hollow Excursions – Business Card</title>
<link rel="stylesheet" href="https://fonts.googleapis.com/css2?family=Cinzel:wght@500&family=Open+Sans:wght@400;600&display=swap">
<style>
  :root {
    --backdrop: #2c2c2e;
    --card: #f7f7f5;
    --vine-green: #1f6b3a;
    --gold: #a8875a;
    --ink: #4a4a4a;
    --watermark-a: rgba(200, 206, 200, 0.55);
    --watermark-b: rgba(247, 247, 245, 0);
    --badge-brown: #8a6a4a;
    --badge-green: #4f9a3a;
    --badge-red: #c9302c;
  }
  * { margin: 0; padding: 0; box-sizing: border-box; }
  html, body { width: 1200px; height: 960px; overflow: hidden; }
  body {
    background: var(--backdrop);
    position: relative;
    font-family: "Open Sans", sans-serif;
  }
  .card {
    position: absolute;
    left: 250px;
    width: 700px;
    height: 400px;
    background: var(--card);
    overflow: hidden;
  }
  .card--back { top: 50px; }
  .card--front { top: 510px; }

  /* Back side */
  .brand {
    position: absolute;
    inset: 0;
    display: flex;
    flex-direction: column;
    align-items: center;
    justify-content: center;
    gap: 22px;
  }
  .brand__mark {
    width: 34px;
    height: 34px;
    background: var(--vine-green);
  }
  .brand__name {
    font-family: "Cinzel", serif;
    font-weight: 500;
    font-size: 36px;
    letter-spacing: 2px;
    color: var(--gold);
  }

  /* Front side */
  .watermark {
    position: absolute;
    left: 40px;
    top: 40px;
    width: 620px;
    height: 300px;
    background: radial-gradient(ellipse at 40% 60%, var(--watermark-a), var(--watermark-b) 70%);
  }
  .social {
    position: absolute;
    top: 100px;
    right: 34px;
    display: flex;
    gap: 8px;
  }
  .social__badge { width: 24px; height: 24px; border-radius: 4px; }
  .social__badge--brown { background: var(--badge-brown); }
  .social__badge--green { background: var(--badge-green); }
  .social__badge--red { background: var(--badge-red); }
  .contact {
    position: absolute;
    left: 250px;
    top: 122px;
    color: var(--ink);
    font-size: 17px;
    line-height: 24px;
  }
  .contact__name {
    font-family: "Cinzel", serif;
    font-weight: 500;
    font-size: 27px;
    color: var(--vine-green);
    line-height: 36px;
    margin-bottom: 4px;
    margin-left: 40px;
  }
  .contact__line { margin-left: 40px; }
  .contact__line--email, .contact__line--web { margin-left: 0; }
  .tagline-band {
    position: absolute;
    left: 0;
    right: 0;
    top: 288px;
    height: 40px;
    background: var(--vine-green);
    border-top: 2px solid var(--card);
    border-bottom: 2px solid var(--card);
    box-shadow: 0 -3px 0 var(--gold), 0 3px 0 var(--gold);
    display: flex;
    align-items: center;
    padding-left: 42px;
  }
  .tagline {
    color: #ffffff;
    font-weight: 600;
    font-size: 17px;
    letter-spacing: 0.2px;
  }
</style>
</head>
<body>
  <section class="card card--back" aria-label="Card back">
    <div class="brand">
      <div class="brand__mark"></div>
      <div class="brand__name">Vine Hollow Excursions</div>
    </div>
  </section>

  <section class="card card--front" aria-label="Card front">
    <div class="watermark" role="img" aria-label="Faint vineyard landscape backdrop"></div>
    <div class="social" aria-label="Social profiles">
      <span class="social__badge social__badge--brown"></span>
      <span class="social__badge social__badge--green"></span>
      <span class="social__badge social__badge--red"></span>
    </div>
    <div class="contact">
      <div class="contact__name">DALE MORTON</div>
      <div class="contact__line">(P) 805-219-6384</div>
      <div class="contact__line contact__line--email">info@vinehollowexcursions.example</div>
      <div class="contact__line contact__line--web">vinehollowexcursions.example</div>
    </div>
    <div class="tagline-band">
      <span class="tagline">An authentic &amp; boutique wine tour experience</span>
    </div>
  </section>
</body>
</html>
```